Investment company needing business card

We are wanting a business card which looks sharp and easy on the eye. We are thinking of having a business card with the logo embossed on it, to really make it stand out. We will only have a small amount of information of the business card, person's name, position, email address and phone number

Contact Information for Business Card

Danielle Frost
Executive Assistant
+64 21 473 5162
danielf@harwickpartners.co.nz

Requirements
Must have
• Embossed logo
Should not have
• Not to be busy

```html
<!DOCTYPE html>
<html lang="en">
<head>
<meta charset="utf-8">
<title>Harwick Partners – Business Card</title>
<link rel="stylesheet" href="https://fonts.googleapis.com/css2?family=Oswald:wght@500;600&family=Roboto:ital,wght@0,400;1,400&display=swap">
<style>
  :root {
    --page-bg: #e9eaea;
    --card-front: #ffffff;
    --card-back: #4b4c4c;
    --brand-green: #1f9d5b;
    --text-grey: #4a4a4a;
    --muted-grey: #8a8a8a;
    --watermark: #eef3f0;
  }
  * { margin: 0; padding: 0; box-sizing: border-box; }
  html, body { width: 1200px; height: 900px; overflow: hidden; }
  body {
    background: var(--page-bg);
    font-family: "Roboto", Arial, sans-serif;
    position: relative;
  }
  .card {
    position: absolute;
    left: 285px;
    width: 630px;
    height: 360px;
    border-radius: 22px;
    overflow: hidden;
    box-shadow: 0 8px 24px rgba(0,0,0,0.18);
  }
  .card--front { top: 60px; background: radial-gradient(ellipse at 60% 45%, #ffffff 0%, #f1f1f1 100%); }
  .card--back { top: 480px; background: var(--card-back); }

  .front__mark {
    position: absolute;
    left: 250px; top: 95px;
    width: 170px; height: 170px;
    background: var(--watermark);
    border-radius: 6px;
  }
  .front__identity {
    position: absolute;
    right: 350px; top: 125px;
    text-align: right;
  }
  .front__name {
    font-family: "Oswald", "Arial Narrow", sans-serif;
    font-weight: 600;
    font-size: 40px;
    line-height: 1;
    color: var(--brand-green);
    text-transform: uppercase;
    letter-spacing: 0.5px;
    white-space: nowrap;
  }
  .front__role {
    margin-top: 8px;
    font-style: italic;
    font-size: 17px;
    color: var(--text-grey);
  }
  .front__divider {
    position: absolute;
    left: 298px; top: 150px;
    width: 2px; height: 72px;
    background: var(--brand-green);
  }
  .front__contacts {
    position: absolute;
    left: 316px; top: 150px;
    list-style: none;
  }
  .front__contacts li {
    display: flex;
    align-items: center;
    gap: 10px;
    font-style: italic;
    font-size: 17px;
    color: var(--text-grey);
    height: 24px;
    white-space: nowrap;
  }
  .front__contacts svg { width: 14px; height: 14px; flex: none; }

  .back__brand {
    position: absolute;
    left: 0; right: 0; top: 140px;
    display: flex;
    align-items: center;
    justify-content: center;
    gap: 18px;
  }
  .back__square {
    width: 44px; height: 44px;
    background: var(--brand-green);
  }
  .back__name {
    font-family: "Oswald", "Arial Narrow", sans-serif;
    font-weight: 600;
    font-size: 50px;
    line-height: 1;
    color: var(--brand-green);
    text-transform: uppercase;
    letter-spacing: 2px;
  }
  .back__rule {
    position: absolute;
    left: 215px; top: 222px;
    width: 200px; height: 2px;
    background: var(--muted-grey);
  }
</style>
</head>
<body>
  <section class="card card--front" aria-label="Card front">
    <div class="front__mark" aria-hidden="true"></div>
    <div class="front__identity">
      <h1 class="front__name">Danielle Frost</h1>
      <p class="front__role">Executive Assistant</p>
    </div>
    <div class="front__divider"></div>
    <ul class="front__contacts">
      <li>
        <svg viewBox="0 0 24 24" aria-hidden="true"><path fill="#1f9d5b" d="M6.6 10.8a15 15 0 0 0 6.6 6.6l2.2-2.2c.3-.3.7-.4 1-.2 1.1.4 2.3.6 3.6.6.6 0 1 .4 1 1V20c0 .6-.4 1-1 1A17 17 0 0 1 3 4c0-.6.4-1 1-1h3.5c.6 0 1 .4 1 1 0 1.3.2 2.5.6 3.6.1.3 0 .7-.2 1z"/></svg>
        +64 21 473 5162
      </li>
      <li>
        <svg viewBox="0 0 24 24" aria-hidden="true"><rect x="2.5" y="5" width="19" height="14" rx="1.5" fill="none" stroke="#1f9d5b" stroke-width="2"/><path d="M3 6l9 7 9-7" fill="none" stroke="#1f9d5b" stroke-width="2"/></svg>
        danielf@harwickpartners.co.nz
      </li>
      <li>
        <svg viewBox="0 0 24 24" aria-hidden="true"><circle cx="12" cy="12" r="9.5" fill="none" stroke="#1f9d5b" stroke-width="2"/><ellipse cx="12" cy="12" rx="4" ry="9.5" fill="none" stroke="#1f9d5b" stroke-width="1.6"/><path d="M2.5 12h19" stroke="#1f9d5b" stroke-width="1.6"/></svg>
        www.harwickpartners.co.nz
      </li>
    </ul>
  </section>

  <section class="card card--back" aria-label="Card back">
    <div class="back__brand">
      <span class="back__square" aria-hidden="true"></span>
      <span class="back__name">Harwick Partners</span>
    </div>
    <div class="back__rule" style="left:auto; right:90px;"></div>
  </section>
</body>
</html>
```